Kestrel Motion LLC Sports Therapy and Soft Tissue Injury solutions

We are a company that specializes in Sports Therapy, Physical therapy, muscular rehab, nutrition plans, and personal training. Kestrel Motion travels around the country and world treating athletes and people in the workforce that have Soft Tissue injuries. We are legally partnered with VMR(Vantor Muscle Recovery/vantorrecovery.example) in treating endurance athletes ex. SteelRidge triathalon. We educate our patients on how to sustain a healthy lifestyle.We need a web design that has a Home page summarizing our services, a Physical therapy page, a Personal training and nutrition page. Our ultimate goal is to build relationships with fitness centers, training facilities, and companies that are implementing preventative health measures for their employees. We want to incorporate the VMR logo and Steelridge logo attached in the website but, we want to use our own name (Kestrel Motion LLC) as the main draw. We will provide literature for the website.

Target Market(s)

Grindlane training gyms, Fitness centers, Dance studios, Companies looking for Corporate Wellness programs

Industry/Entity Type

Health And Wellness

Number of Pages Required

4 page

Font styles to use
Sans Serif

Requirements
Must have
• Stock Photos of Athletes training. Examples of Endurance Athletes and Cross training. A mesh of as many sports and training methods as possible. We are a new company and don't have many photos. Easy accessibility to change and add text as the company grows. Vantor Muscle recovery logo incorporated in the back ground of the website. Always visible but does not take over the web page
Nice to have
• Sleek and cool, and masculine design. We want the website to stand out without focusing on one individual. We want to use the website to brand the company (Kestrel Motion LLC) with easy access to social media platforms

```html
<!DOCTYPE html>
<html lang="en">
<head>
<meta charset="utf-8">
<title>Kestrel Motion LLC</title>
<link rel="stylesheet" href="https://fonts.googleapis.com/css2?family=Oswald:wght@400;500&family=Nunito:wght@400;600&family=Open+Sans:wght@400;600&display=swap">
<style>
:root{
  --blue:#1a6fb8;
  --blue-dark:#1560a3;
  --link:#2a86d0;
  --ink:#222;
  --muted:#8a8a8a;
  --light:#f2f2f2;
  --footer:#1b1b1b;
  --footer-bottom:#121212;
  --white:#fff;
  --partner:#9a9a9a;
}
*{margin:0;padding:0;box-sizing:border-box}
html,body{width:1200px;height:2449px;overflow:hidden}
body{position:relative;font-family:"Open Sans",Arial,sans-serif;color:var(--ink);background:var(--white)}
h1,h2,h3,h4{font-weight:400}
.abs{position:absolute}
.topbar{left:0;top:0;width:1200px;height:33px;background:var(--blue);color:var(--white);font-size:13px}
.topbar .contact{position:absolute;top:8px;display:flex;align-items:center;gap:6px}
.topbar svg{display:block}
.sq{width:13px;height:13px;background:var(--white);border-radius:2px;display:inline-block}
.header{left:0;top:33px;width:1200px;height:106px;background:var(--white)}
.logo{position:absolute;left:88px;top:33px;font-family:"Oswald",sans-serif;font-weight:500;font-size:30px;color:var(--blue);letter-spacing:.2px}
.nav{position:absolute;left:380px;top:43px;display:flex;gap:36px;font-family:"Nunito",sans-serif;font-size:14px;color:#333;text-transform:uppercase}
.nav .active{color:var(--blue);border-bottom:2px solid var(--blue);padding-bottom:3px}
.hero{left:0;top:139px;width:1200px;height:550px;background:linear-gradient(180deg,#244f8f 0%,#4d7fbf 30%,#6f97c8 45%,#5f8b3e 58%,#6f9a48 74%,#8c6456 86%,#7d5a50 100%)}
.hero-title{right:85px;top:495px;font-family:"Oswald",sans-serif;font-size:46px;color:var(--white);text-align:right;line-height:1}
.hero-sub{right:85px;top:556px;font-family:"Open Sans",sans-serif;font-size:24px;color:var(--white)}
.hero-arrow{top:612px;width:26px;height:26px;border-radius:50%;background:rgba(0,0,0,.45);border:1px solid rgba(255,255,255,.7)}
.section-title{font-family:"Nunito",sans-serif;font-size:26px;color:#111;text-transform:uppercase}
.service{width:230px;text-align:center}
.service .ring{width:164px;height:164px;border-radius:50%;margin:0 auto;background:radial-gradient(circle,#fff 62%,#f3f3f3 100%);border:1px solid #eaeaea;box-shadow:0 0 0 5px #f7f7f7;display:flex;align-items:center;justify-content:center}
.service h3{margin-top:32px;font-family:"Nunito",sans-serif;font-size:18px;color:#222;text-transform:uppercase}
.service p{margin-top:6px;font-size:13px;color:var(--muted);line-height:20px;padding:0 2px}
.service a,.blog a{color:var(--link);text-decoration:none}
.service a{display:block;margin-top:6px;font-size:12px}
.about{left:0;top:1236px;width:1200px;height:394px;background:linear-gradient(100deg,#1f72c2 0%,#2a7bc8 55%,#1e67b0 100%)}
.about-photo{left:90px;top:1302px;width:434px;height:272px;border:2px solid rgba(255,255,255,.8);background:linear-gradient(180deg,#4a4f57 0%,#8e949b 40%,#6d6258 62%,#3a3431 100%)}
.about-body{left:563px;top:1310px;width:547px;display:flex;flex-direction:column;align-items:flex-start}
.about-title{font-family:"Nunito",sans-serif;font-size:26px;color:var(--white);text-transform:uppercase;line-height:34px}
.about-text{margin-top:10px;font-size:12.6px;line-height:22.4px;color:var(--white);text-align:justify}
.btn{margin-top:14px;width:118px;height:34px;border-radius:17px;background:var(--white);color:#222;font-size:13px;display:flex;align-items:center;justify-content:center;text-transform:uppercase}
.blog-band{left:0;top:1630px;width:1200px;height:362px;background:var(--light)}
.blog-title{left:91px;top:1702px;font-family:"Nunito",sans-serif;font-size:21px;color:#111;text-transform:uppercase}
.blog-nav{left:1090px;top:1692px;font-size:20px;color:#111}
.blog-img{width:164px;height:132px}
.blog{width:310px}
.blog h4{font-size:13px;color:#222}
.blog .date{margin-top:9px;font-size:12.5px;color:#222}
.blog p{margin-top:9px;font-size:11px;line-height:19.6px;color:#666}
.blog a{display:block;margin-top:6px;font-size:12px}
.partner{top:2052px;font-size:30px;color:var(--partner);transform:translateX(-50%);white-space:nowrap;font-family:"Oswald",sans-serif}
.footer{left:0;top:2147px;width:1200px;height:221px;background:var(--footer);color:var(--white)}
.footer-bottom{left:0;top:2368px;width:1200px;height:81px;background:var(--footer-bottom)}
.foot-head{font-family:"Nunito",sans-serif;font-size:16px;color:var(--white);text-transform:uppercase}
.foot-text{font-size:12.5px;color:#ddd;line-height:23px}
.links li{list-style:none;font-size:12.5px;color:#ddd;line-height:25px}
.links li::before{content:"";display:inline-block;border-left:5px solid #ddd;border-top:4px solid transparent;border-bottom:4px solid transparent;margin-right:8px}
.partner-mark{font-family:"Open Sans",sans-serif;font-weight:600;color:var(--white)}
.field{left:905px;top:2267px;width:147px;height:29px;background:var(--white);color:#888;font-size:11.5px;padding:7px 12px}
.submit{left:1052px;top:2267px;width:55px;height:29px;background:var(--blue);color:var(--white);font-size:11.5px;display:flex;align-items:center;justify-content:center}
.social{top:2391px;width:26px;height:26px;background:var(--blue)}
</style>
</head>
<body>

<div class="abs topbar">
  <div class="contact" style="left:91px">
    <svg width="12" height="12" viewBox="0 0 24 24"><path fill="#fff" d="M6.6 10.8a15 15 0 0 0 6.6 6.6l2.2-2.2c.3-.3.7-.4 1-.2 1.1.4 2.3.6 3.6.6.6 0 1 .4 1 1V20c0 .6-.4 1-1 1A17 17 0 0 1 3 4c0-.6.4-1 1-1h3.5c.6 0 1 .4 1 1 0 1.3.2 2.5.6 3.6.1.3 0 .7-.2 1z"/></svg>
    <span>: +64-9-5550142</span>
  </div>
  <div class="contact" style="left:240px">
    <svg width="14" height="11" viewBox="0 0 24 18"><rect width="24" height="18" rx="2" fill="#fff"/><path d="M1 2l11 8 11-8" stroke="#1a6fb8" stroke-width="2" fill="none"/></svg>
    <span>: info@kestrelmotion.example</span>
  </div>
  <div class="contact" style="left:978px">
    <svg width="14" height="14" viewBox="0 0 24 24"><circle cx="10" cy="10" r="7" stroke="#fff" stroke-width="3" fill="none"/><path d="M15 15l7 7" stroke="#fff" stroke-width="3"/></svg>
  </div>
  <div class="contact" style="left:1031px;gap:5px">
    <span class="sq"></span><span class="sq"></span><span class="sq"></span><span class="sq"></span>
  </div>
</div>

<header class="abs header">
  <div class="logo">KESTREL MOTION LLC</div>
  <nav class="nav">
    <span class="active">Home</span><span>Services</span><span>Physical Therapy</span><span>Personal Training</span><span>Nutrition</span><span>Contact Us</span>
  </nav>
</header>

<section class="abs hero" role="img" aria-label="Sprinter bursting off the start on a stadium track"></section>
<div class="abs hero-title">KESTREL MOTION TRAVELS</div>
<div class="abs hero-sub">Neque porro quisquam est qui dolorem</div>
<div class="abs hero-arrow" style="left:90px"><svg width="24" height="24" viewBox="0 0 24 24"><path d="M14 7l-5 5 5 5" stroke="#fff" stroke-width="2" fill="none"/></svg></div>
<div class="abs hero-arrow" style="left:122px"><svg width="24" height="24" viewBox="0 0 24 24"><path d="M10 7l5 5-5 5" stroke="#fff" stroke-width="2" fill="none"/></svg></div>

<h2 class="abs section-title" style="left:0;width:1200px;text-align:center;top:771px">Feature Our Services</h2>

<div class="abs service" style="left:86px;top:857px">
  <div class="ring"><svg width="64" height="64" viewBox="0 0 64 64" fill="#1a6fb8"><circle cx="42" cy="12" r="6"/><path d="M28 20h14l6 12h8v5H45l-4-7-5 10 8 8-4 4-11-10-6 12H13l8-17 6-12h-5l-5 7-4-3 7-9z"/></svg></div>
  <h3>Sports Therapy</h3>
  <p>We are a company that specializes in Sports Therapy, Physical therapy,</p>
  <a>Read More -&gt;</a>
</div>
<div class="abs service" style="left:359px;top:857px">
  <div class="ring"><svg width="64" height="64" viewBox="0 0 64 64" fill="#1a6fb8"><circle cx="20" cy="12" r="6"/><path d="M14 20h12l6 10-4 3-5-6v8h-9z"/><rect x="22" y="40" width="36" height="10" rx="5"/><circle cx="14" cy="45" r="6"/></svg></div>
  <h3>Physical Therapy</h3>
  <p>We are a company that specializes in Sports Therapy, Physical therapy,</p>
  <a>Read More -&gt;</a>
</div>
<div class="abs service" style="left:625px;top:857px">
  <div class="ring"><svg width="64" height="64" viewBox="0 0 64 64" fill="#1a6fb8"><circle cx="26" cy="10" r="6"/><path d="M18 18h14l8 12-4 3-6-8-2 11h-8z"/><rect x="8" y="40" width="50" height="8" rx="4"/><circle cx="52" cy="34" r="5"/><rect x="10" y="50" width="4" height="8"/><rect x="52" y="50" width="4" height="8"/></svg></div>
  <h3>Muscular Rehab</h3>
  <p>We are a company that specializes in Sports Therapy, Physical therapy,</p>
  <a>Read More -&gt;</a>
</div>
<div class="abs service" style="left:896px;top:857px">
  <div class="ring"><svg width="64" height="64" viewBox="0 0 64 64" fill="#1a6fb8"><circle cx="26" cy="10" r="6"/><path d="M22 20l8-2 6 14 12-6 2 5-16 9-2-4-4 14 8 10-5 3-10-12 4-16-9 4-2-5z"/></svg></div>
  <h3>Nutrition Plans</h3>
  <p>We are a company that specializes in Sports Therapy, Physical therapy,</p>
  <a>Read More -&gt;</a>
</div>

<section class="abs about"></section>
<div class="abs about-photo" role="img" aria-label="Runner crouched on a road under a stormy sky"></div>
<div class="abs about-body">
  <h2 class="about-title">About Kestrel Motion LLC</h2>
  <p class="about-text">At Kestrel Motion we focus on our ability to train individuals from beginners to elite athletes. We have everything you here to attain your fitness goals! False advertisements, 3 month workout fads, insane diets pills, and Elective Surgery are not the way to a healthy sustainable lifestyle. Affordable training is on a person by person basis and comes with nutrition At Kestrel Motion we focus on our ability to train individuals from beginners to elite athletes. We have everything you here to attain your fitness goals! False advertisements, 3 month workout fads, insane diets pills, and Elective Surgery</p>
  <div class="btn">Read More</div>
</div>

<section class="abs blog-band"></section>
<h2 class="abs blog-title">Latest Blog</h2>
<div class="abs blog-nav">&lsaquo;&rsaquo;</div>

<div class="abs blog-img" style="left:91px;top:1759px;background:linear-gradient(90deg,#c9a27a 0%,#8a6040 55%,#5a4030 100%)" role="img" aria-label="Climber scaling a rock face"></div>
<article class="abs blog" style="left:271px;top:1758px">
  <h4>Nemo Enim Ipsam Volup</h4>
  <div class="date">09-07-2016</div>
  <p>Lorem Ipsum has been the industry's standard dummy text ever since the 1500s, when an unknown printer took a galley of type and scrambled it to make a type specimen book.</p>
  <a>Read More &gt;&gt;</a>
</article>

<div class="abs blog-img" style="left:627px;top:1757px;background:linear-gradient(180deg,#b9c9d6 0%,#9aa892 55%,#6e7a66 100%)" role="img" aria-label="Couple jogging together on a country road"></div>
<article class="abs blog" style="left:807px;top:1756px">
  <h4>Nemo Enim Ipsam Volup</h4>
  <div class="date">09-07-2016</div>
  <p>Lorem Ipsum has been the industry's standard dummy text ever since the 1500s, when an unknown printer took a galley of type and scrambled it to make a type specimen book.</p>
  <a>Read More &gt;&gt;</a>
</article>

<div class="abs partner" style="left:155px">BRISK</div>
<div class="abs partner" style="left:314px">Aurevo</div>
<div class="abs partner" style="left:469px">ENVOYANT</div>
<div class="abs partner" style="left:645px">Qelvra</div>
<div class="abs partner" style="left:828px">verda</div>
<div class="abs partner" style="left:1004px">FLOWEN</div>

<footer class="abs footer"></footer>
<div class="abs partner-mark" style="left:90px;top:2212px;font-size:34px;line-height:1">VMR</div>
<div class="abs partner-mark" style="left:90px;top:2254px;font-size:11px">Vantor Muscle Recovery</div>
<div class="abs partner-mark" style="left:90px;top:2274px;font-size:10px;font-weight:400">PROUD PARTNER</div>
<div class="abs partner-mark" style="left:90px;top:2288px;font-size:24px;line-height:1.2">SteelRidge</div>

<h3 class="abs foot-head" style="left:376px;top:2186px">Links</h3>
<ul class="abs links" style="left:376px;top:2222px">
  <li>Physical Therapy</li><li>Personal Training</li><li>Nutrition</li><li>Services</li>
</ul>

<h3 class="abs foot-head" style="left:586px;top:2186px">Get In Touch</h3>
<div class="abs foot-text" style="left:586px;top:2223px">Address : 2280 W. Larkspur Ave Suite 410<br>Fairhaven, California, 90000</div>
<div class="abs foot-text" style="left:586px;top:2275px">Phone : (555)014-7720</div>
<div class="abs foot-text" style="left:586px;top:2301px">Email : info@kestrelmotion.example</div>

<h3 class="abs foot-head" style="left:905px;top:2186px">Newsletter</h3>
<div class="abs foot-text" style="left:905px;top:2220px;width:220px;font-size:11.5px;line-height:18px">Your about us information would fit here nicely.</div>
<div class="abs field">Email address</div>
<div class="abs submit">Submit</div>

<div class="abs footer-bottom"></div>
<div class="abs" style="left:88px;top:2395px;font-size:13px;color:var(--white)">Copyright © 2017. All Rights Reserved</div>
<div class="abs social" style="left:974px"></div>
<div class="abs social" style="left:1011px"></div>
<div class="abs social" style="left:1046px"></div>
<div class="abs social" style="left:1080px"></div>

</body>
</html>
```